Australian Trucking Company Requires Professional Looking Stationary

We require a professional looking stationary design that incorporates our newly designed logo.

Our business, called "Brell Haulage Contracting", provides contracting work, transport and logistics to business in Western Australia particularly with links to the mining sector.

We are a small business looking to expand and our new logo and our new stationary will help develop our brand image in our market place.

Target Market(s)

Businesses and Corporation with links to the Mining Sector

Industry/Entity Type

Small Business

Requirements
Must have
• The letterhead must have the following details:
The new logo

Text saying: "Brell Holdings Pty Ltd (ACN 582 316 907) ATF The Brell Discretionary Trust T/AS"
"ABN 71 834 209 553"
Address "P.O Box 817 Wattlegrove WA, 6958"
Phone: 08 9352 7140
Email: brellhaul@mailbox-example.com.au

The text on the letterhead should be editable as the details are likely to change in the near future. Provision should be made for a website address all though one isn't available at the moment.

The styling, layout and font text is entirely up to the designer.

```html
<!DOCTYPE html>
<html lang="en">
<head>
<meta charset="utf-8">
<title>Brell Haulage Contracting – Business Cards</title>
<link href="https://fonts.googleapis.com/css2?family=Arimo:wght@400;700&display=swap" rel="stylesheet">
<style>
  :root {
    --brand-red: #e3141b;
    --ink-grey: #8a8a8a;
    --panel-dark: #555555;
    --panel-darker: #3f3f3f;
    --card-white: #ffffff;
    --stage: #ececec;
    --grey-light: #d9d9d9;
    --grey-mid: #8c8c8c;
    --grey-deep: #4a4a4a;
  }
  * { box-sizing: border-box; margin: 0; padding: 0; }
  html, body { width: 1200px; height: 665px; overflow: hidden; }
  body {
    background: var(--stage);
    font-family: "Arimo", Arial, sans-serif;
    position: relative;
  }
  .card {
    position: absolute;
    top: 178px;
    width: 540px;
    height: 310px;
    border-radius: 28px;
    overflow: hidden;
    box-shadow: 0 6px 18px rgba(0,0,0,0.25);
  }

  /* ---------- Front ---------- */
  .card--front {
    left: 40px;
    background: linear-gradient(90deg, var(--card-white) 0 305px, var(--grey-light) 305px, var(--grey-mid) 100%);
  }
  .front__name {
    position: absolute;
    right: 310px;
    top: 28px;
    color: var(--brand-red);
    font-weight: 700;
    font-size: 15px;
  }
  .front__title-block {
    position: absolute;
    left: 240px;
    top: 0;
    width: 65px;
    height: 68px;
    background: var(--panel-dark);
    color: #e8e8e8;
    font-size: 11px;
    padding: 16px 0 0 22px;
  }
  .logo-band {
    position: absolute;
    background: var(--card-white);
    box-shadow: 0 8px 14px rgba(0,0,0,0.28);
    display: flex;
    align-items: center;
  }
  .card--front .logo-band {
    left: 70px;
    top: 68px;
    width: 405px;
    height: 150px;
    padding-left: 40px;
    gap: 26px;
  }
  .logo-mark {
    width: 56px;
    height: 56px;
    background: var(--grey-deep);
    flex: none;
  }
  .logo-name {
    color: var(--brand-red);
    font-weight: 700;
    text-transform: uppercase;
    line-height: 1.02;
    letter-spacing: 0.5px;
  }
  .card--front .logo-name { font-size: 28px; }
  .front__address {
    position: absolute;
    right: 245px;
    top: 232px;
    text-align: right;
    color: var(--ink-grey);
    font-size: 12px;
    line-height: 1.35;
  }
  .front__abn {
    position: absolute;
    right: 245px;
    top: 276px;
    color: var(--ink-grey);
    font-size: 12px;
  }
  .contact-panel {
    position: absolute;
    left: 305px;
    top: 218px;
    width: 170px;
    height: 92px;
    background: linear-gradient(180deg, var(--panel-dark), var(--panel-darker));
    padding: 14px 0 0 14px;
    list-style: none;
  }
  .contact-panel li {
    display: flex;
    align-items: center;
    gap: 6px;
    color: #eeeeee;
    font-size: 10.5px;
    height: 21px;
    white-space: nowrap;
  }
  .contact-panel svg { width: 11px; height: 11px; flex: none; }

  /* ---------- Back ---------- */
  .card--back {
    left: 620px;
    background: radial-gradient(ellipse at 55% 40%, #a8a8a8 0%, #6e6e6e 45%, #3e3e3e 100%);
  }
  .card--back .logo-band {
    left: 30px;
    top: 52px;
    width: 480px;
    height: 206px;
    flex-direction: column;
    align-items: stretch;
    justify-content: center;
  }
  .back__logo {
    display: flex;
    align-items: center;
    gap: 30px;
    padding-left: 60px;
  }
  .card--back .logo-mark { width: 66px; height: 66px; }
  .card--back .logo-name { font-size: 34px; }
  .back__legal {
    margin-top: 22px;
    padding-left: 14px;
    color: var(--ink-grey);
    font-size: 10.5px;
  }
</style>
</head>
<body>

  <section class="card card--front" aria-label="Business card front">
    <p class="front__name">Name here</p>
    <div class="front__title-block">Title</div>

    <div class="logo-band">
      <span class="logo-mark" aria-hidden="true"></span>
      <p class="logo-name">Brell<br>Haulage<br>Contracting</p>
    </div>

    <p class="front__address">P.O Box 817 Wattlegrove WA,<br>6958</p>
    <p class="front__abn">ABN 71 834 209 553</p>

    <ul class="contact-panel">
      <li>
        <svg viewBox="0 0 24 24" fill="none" stroke="#eee" stroke-width="2.4"><circle cx="12" cy="12" r="10"/><path d="M8 7l2 3-1 1.5c.8 1.6 2 2.8 3.5 3.5L14 14l3 2-1.5 2C11 18 6 13 6 8.5z" fill="#eee" stroke="none"/></svg>
        08 9352 7140
      </li>
      <li>
        <svg viewBox="0 0 24 24"><rect x="2" y="5" width="20" height="14" fill="#eee"/><path d="M2 5l10 8 10-8" fill="none" stroke="#555" stroke-width="2"/></svg>
        brellhaul@mailbox-example.com.au
      </li>
      <li>
        <svg viewBox="0 0 24 24" fill="none" stroke="#eee" stroke-width="2"><circle cx="12" cy="12" r="10"/><ellipse cx="12" cy="12" rx="4.5" ry="10"/><path d="M2 12h20M4 7h16M4 17h16"/></svg>
        www.brellhaulage-example.com
      </li>
    </ul>
  </section>

  <section class="card card--back" aria-label="Business card back">
    <div class="logo-band">
      <div class="back__logo">
        <span class="logo-mark" aria-hidden="true"></span>
        <p class="logo-name">Brell<br>Haulage<br>Contracting</p>
      </div>
      <p class="back__legal">Brell Holdings Pty Ltd (ACN 582 316 907) ATF The Brell Discretionary Trust T/AS</p>
    </div>
  </section>

</body>
</html>
```